Yoga/movement guide/teacher for adult yoga practice and kid yoga

What is the positioning or mission statement of your company? to guide individuals in a yoga-based safe and sustainable movement practice applicable to all ages and body types. Currently my focus is working with children in daycare and school settings, but my goal is to expand into private yoga practice for adults, and potentially as part of rented space in studios. I hope to find a way to work with children AND adults (so would love for logo to be appealing to both), but current focus is with children based on need and demand in the community. yoga for children also compliments my backround as a pediatrician/neonatologist, and I greatly miss interacting with children. I also want to emphasize a yoga/movement practice that is focused more on what one feels internally through movement. NOT what one looks like asthetically. I believe in removing all mirrors from yoga/movement practice. It should be an experience of movement/poses/yoga through appropriate cueing and education. It is not about the details of how far the knee should bend, or how high the leg should be. Focusing on foudation first, core, then core engagement and ultimately expression of poses/movements. A focus on strength, stability and mobility, not just flexibility, which is the common perception/association with yoga. I also want individuals to learn to be an advocate of their own health. Through guidance, I hope for individuals to connect with their body so they know themselves so well to be able to advocate for themselves in the modern healthcare world. This internal experience and connection is so essential in a world where modern medicine has become a business and it is all about making a dollar. the connection with patients is lost, and individuals need to learn to empower themselves and through their new found voice to be able to articulate what is wrong.<br/>Does your company have a tagline or slogan that should be included with the logo? "Move With Inner Light"<br/>What do you hope your company can be known for? Accessible yoga for a sustained practice. A guided movement practice where one gains information and knowledge of oneself through a mind/body connection. For one feel good physically with a new awaraness of their internal radiance that exists in all beings. Physical rejuvenation egnites a light and increases energy to flow through the physical body, which ultimately tranlates into works of kindness for others and out in the world. <br/>What color palettes might you prefer? why? love the colors currently chosen<br/>Where will the logo be primarily used? initially business cards, but hopefully future websites, t-shirts, and potentially local magazine adds. Also starting with a small couple of banners for community events in the area. I currently practice as a nomad out of my car :)<br/>Are there any elements you would prefer to see in the logo? Movement. A modern depiction of a human body/figure practicing movement. Hoping to avoid a stereotypical yoga pose per say, just because I want to people to think of it more of a movement practice with yoga roots. Modern yoga. There are elements of breathing and connecting with oneself through the flow of breath and movement, but I do not focus on the meditative/cerebral aspect of the yoga practice. What I teach is almost reaching a meditative state through movement. I personally don't practice, nor resonate with just seated meditation. just not my thing :)<br/>In your opinion, what defines a well-designed logo? curiosity. enough info for individuals to think they know what it means, but want to know more. invokes curiosity, but not too abstract. Reproducible. not too complicated. I want also to invoke a community feel, so a design that appeals to all people within a community. <br/>What is your preference in reference to icons, typography, spokespeople (characters), etc.? modern design. I love the idea of a logo for my purposes, to invoke a sense of movement from within. So not too static. <br/>What words or icons must be included in the logo? movement with yoga roots. <br/>What logos do you like and why? A representation, but not exact. I think some ambiguity is intriguing for others, and also memorable. I want it to be an artistic representation of movement/yoga<br/>What logos do you dislike and why? too busy, too loud. <br/>In your opinion, what is the primary purpose for a logo? association<br/>Who is the primary target audience? (who is most likely to use your services/product?) Children and their parents, but ultimately to expand into teaching adults. I even have aspirations of prenatal and post-natal yoga. Potentially incorporating infants. <br/>Who currently uses your product the most? n/a (working in schools/daycare currently. It is currently all volunteer)<br/>Are you pleased with the range of people your company serves? n/a<br/>Are you looking to expand, modify, or completely change your target audience? or will it remain the same? yes! expand into an adult audience. <br/>How do you plan to focus on your target audience? currently by working through schools and daycares. hopefully ultimately through after school care programs and then offering kid yoga in an existing yoga studio (working on this with Q Studio in Ridgeland, currently)<br/>What are your main forms of advertising? word of mouth, schools, daycares. Happy kids talking to their parents about the yoga class they took and happy teachers :)<br/>How do most customers find out about your company?<br/>Which gender are you targeting? All genders! However, with kid yoga, often the maternal individual in the child's life is more involved with decision making as far as extracurricular activities

Target Market(s)

individuals and families interested in wellness and feeling great

Contact Information for Business Card

Dana Whitford
Yoga Instructor
RYT-200, RCYT

certified yoga teacher for adults and children

Colors

Designer to choose colors to be used in the design.

Requirements
Must have
• "Move With Inner Light"
Nice to have
• logo with same colors

```html
<!DOCTYPE html>
<html lang="en">
<head>
<meta charset="utf-8">
<title>Bright Path Studios – Business Card</title>
<link href="https://fonts.googleapis.com/css2?family=Short+Stack&family=Josefin+Sans:wght@300;400&family=Arimo:wght@400&display=swap" rel="stylesheet">
<style>
  :root {
    --page-bg: #151617;
    --card-bg: #383b3d;
    --pattern-bg: #3c3f41;
    --pattern-glow: #45484a;
    --sun-yellow: #f6dc3a;
    --sea-teal: #5ec9d2;
    --ink-white: #f4f4f4;
  }
  * { box-sizing: border-box; margin: 0; padding: 0; }
  html, body {
    width: 1200px; height: 900px; overflow: hidden;
    background: var(--page-bg);
  }
  .canvas {
    width: 1200px; height: 900px;
    display: flex; flex-direction: column;
    align-items: center; justify-content: center; gap: 40px;
  }
  .card {
    width: 700px; height: 400px;
    background: var(--card-bg);
    position: relative; overflow: hidden;
  }

  /* Front side */
  .card-front .pattern-field {
    position: absolute; inset: 0;
    background: radial-gradient(circle at 40% 45%, var(--pattern-glow), var(--pattern-bg) 70%);
  }
  .card-front .brand-mark {
    position: absolute; inset: 0;
    display: flex; align-items: center; justify-content: center; gap: 18px;
  }
  .brand-dot {
    width: 46px; height: 46px; border-radius: 50%;
    background: var(--sun-yellow);
  }
  .brand-name {
    font-family: "Short Stack", cursive;
    color: var(--sun-yellow);
    font-size: 40px; line-height: 1;
  }

  /* Back side */
  .card-back {
    display: flex; align-items: center;
    padding-left: 95px;
  }
  .logo-block { width: 200px; }
  .logo-block .brand-name { font-size: 28px; line-height: 1.15; }
  .tagline {
    margin-top: 12px;
    font-family: "Josefin Sans", sans-serif; font-weight: 400;
    font-size: 9px; letter-spacing: 2px;
    color: var(--sea-teal); text-transform: uppercase;
  }
  .divider {
    width: 2px; height: 150px;
    background: var(--sea-teal);
    margin: 0 28px 0 24px;
  }
  .contact-block { color: var(--ink-white); }
  .person-name {
    font-family: "Short Stack", cursive;
    color: var(--sun-yellow); font-size: 27px; line-height: 1.1;
  }
  .person-role {
    font-family: "Josefin Sans", sans-serif; font-weight: 400;
    color: var(--sea-teal); font-size: 19px; margin-bottom: 18px;
  }
  .contact-list { list-style: none; font-family: "Arimo", sans-serif; font-size: 19px; }
  .contact-list li { display: flex; align-items: center; gap: 10px; line-height: 1.45; }
  .contact-icon { width: 18px; height: 18px; flex: none; }
  .contact-icon * { fill: none; stroke: var(--sea-teal); stroke-width: 1.6; }
</style>
</head>
<body>
<main class="canvas">

  <section class="card card-front">
    <div class="pattern-field" role="img" aria-label="Repeating pattern of small grey spirals across the card"></div>
    <div class="brand-mark">
      <span class="brand-dot"></span>
      <span class="brand-name">Bright Path</span>
    </div>
  </section>

  <section class="card card-back">
    <div class="logo-block">
      <div class="brand-name">Bright Path Studios</div>
      <div class="tagline">Move With Inner Light</div>
    </div>
    <div class="divider"></div>
    <div class="contact-block">
      <div class="person-name">Dana Whitford</div>
      <div class="person-role">Owner-Operator</div>
      <ul class="contact-list">
        <li>
          <svg class="contact-icon" viewBox="0 0 20 20"><circle cx="10" cy="10" r="8.5"/><path d="M7 6 L8.5 6 L9.3 8.2 L8.3 9 Q9.3 11 11 11.7 L11.8 10.7 L14 11.5 L14 13 Q10 14 7 9.5 Z"/></svg>
          555-014-2290
        </li>
        <li>
          <svg class="contact-icon" viewBox="0 0 20 20"><rect x="2" y="4.5" width="16" height="11"/><path d="M2 4.5 L10 11 L18 4.5"/></svg>
          Danawhitford@mailbox.com
        </li>
        <li>
          <svg class="contact-icon" viewBox="0 0 20 20"><circle cx="10" cy="10" r="8"/><ellipse cx="10" cy="10" rx="3.5" ry="8"/><path d="M2 10 H18 M3.5 6 H16.5 M3.5 14 H16.5"/></svg>
          www.brightpathstudios.com
        </li>
      </ul>
    </div>
  </section>

</main>
</body>
</html>
```